English and Spanish Language School Needs a Business Card

Need a business card design a startup company called Maribel Language School. The company will offer English and Spanish conversational level courses designed to make the learner feel comfortable with grammar and vocabulary. We would like to see a logo with some colour that should communicate learning, growth.

Target Market(s)

Consumers and businesses

Industry/Entity Type

Education

Contact Information for Business Card

TBD

Font styles to use
Serif

Requirements
Must have
• Include the following
• Logo
• Name
• Title
• Cellphone Number
• Office Phone number
• Email address
• Office Address

```html
<!DOCTYPE html>
<html lang="en">
<head>
<meta charset="utf-8">
<title>Maribel Language School – Business Card</title>
<link rel="stylesheet" href="https://fonts.googleapis.com/css2?family=Tinos:wght@400;700&display=swap">
<style>
  :root {
    --page-bg: #d8d3cb;
    --card-bg: #ecebe8;
    --card-edge: #c9c6c0;
    --brand-red: #a3151c;
    --brand-red-light: #bf2a2f;
    --accent-teal: #1f8583;
    --ink-on-red: #f3dcd3;
    --icon-fill: #e9d3c6;
  }
  * { margin: 0; padding: 0; box-sizing: border-box; }
  html, body {
    width: 1200px; height: 970px; overflow: hidden;
    background: var(--page-bg);
    font-family: "Tinos", "Times New Roman", serif;
  }
  .card {
    position: absolute; left: 100px; top: 199px;
    width: 1000px; height: 572px;
    background: var(--card-bg);
    border: 1px solid var(--card-edge);
    overflow: hidden;
  }
  .card-graphics { position: absolute; inset: 0; }
  .brand {
    position: absolute; left: 53px; top: 62px;
    color: var(--brand-red); font-weight: 400;
  }
  .brand-name { font-size: 118px; line-height: 1; letter-spacing: -1px; }
  .brand-tagline { font-size: 36px; line-height: 1.1; margin-top: 4px; padding-left: 40px; }
  .contact {
    position: absolute; right: 38px; top: 248px;
    text-align: right; color: var(--ink-on-red);
  }
  .person-name { font-size: 38px; font-weight: 700; letter-spacing: 1px; line-height: 1; }
  .person-title { font-size: 27px; line-height: 1.1; margin-top: 2px; }
  .address { font-size: 27px; line-height: 36px; margin-top: 44px; letter-spacing: .5px; }
  .lines { margin-top: 16px; list-style: none; }
  .lines li {
    display: flex; justify-content: flex-end; align-items: center;
    gap: 18px; font-size: 27px; line-height: 34px;
  }
  .icon { width: 28px; height: 28px; flex: none; }
</style>
</head>
<body>
  <div class="card">
    <svg class="card-graphics" width="1000" height="572" viewBox="0 0 1000 572">
      <defs>
        <linearGradient id="redPanel" x1="0" y1="1" x2="1" y2="0">
          <stop offset="0" stop-color="var(--brand-red-light)"/>
          <stop offset="0.5" stop-color="var(--brand-red)"/>
          <stop offset="1" stop-color="var(--brand-red-light)"/>
        </linearGradient>
      </defs>
      <polygon points="883,0 1000,0 1000,572 212,572" fill="url(#redPanel)"/>
      <line x1="851" y1="0" x2="183" y2="572" stroke="var(--accent-teal)" stroke-width="2.5"/>
    </svg>

    <div class="brand">
      <div class="brand-name">Maribel</div>
      <div class="brand-tagline">Language School</div>
    </div>

    <div class="contact">
      <div class="person-name">DANIEL REYES</div>
      <div class="person-title">Manager</div>
      <div class="address">Your Address,2nd Ste<br>Lakeview, Texas 1234</div>
      <ul class="lines">
        <li>123 456 7890
          <svg class="icon" viewBox="0 0 28 28" aria-label="Mobile phone">
            <rect width="28" height="28" fill="var(--icon-fill)"/>
            <rect x="9" y="4" width="10" height="20" rx="2" fill="none" stroke="var(--brand-red)" stroke-width="2"/>
            <rect x="11" y="7" width="6" height="6" fill="var(--brand-red)"/>
          </svg>
        </li>
        <li>123 456 7890
          <svg class="icon" viewBox="0 0 28 28" aria-label="Office phone">
            <rect width="28" height="28" fill="var(--icon-fill)"/>
            <path d="M5 11 Q14 4 23 11 L20 13 L17 10 L11 10 L8 13 Z" fill="var(--brand-red)"/>
            <rect x="7" y="14" width="14" height="9" rx="1" fill="var(--brand-red)"/>
          </svg>
        </li>
        <li>your@yourcompany.com
          <svg class="icon" viewBox="0 0 28 28" aria-label="Email">
            <rect width="28" height="28" fill="var(--icon-fill)"/>
            <rect x="5" y="8" width="18" height="12" fill="none" stroke="var(--brand-red)" stroke-width="2"/>
            <path d="M5 8 L14 15 L23 8" fill="none" stroke="var(--brand-red)" stroke-width="2"/>
          </svg>
        </li>
      </ul>
    </div>
  </div>
</body>
</html>
```